Creation of an elegant and modern turnkey Shopify website

Hello,

We are a new company specializing in the sale of above-ground pools. We want to create a turnkey website, ideally using Shopify. For now, we need a "showcase" site, not an e-commerce platform, with four tabs:

Home Page (an overall presentation of the company)
Our Products (an overview of all the above-ground pools we sell)
Our Projects (a page inspired by Instagram to showcase photos of our future projects)
Contact (a page with all our contact information and a contact form)

We are looking to create a highly visual, elegant, and modern website with vibrant splashes of color. We will provide the text, photos (along with instructions on where to place them on each page), and all other necessary information as attachments.

Thank you in advance for your proposals!

The Brisa Lagoon Team

Target Market(s)

Targeted at Swiss customers (a translator will need to be installed for different languages)

Industry/Entity Type

Sale of customised above-ground pools

Coding

Coded - Design and coding required

Font styles to use
Sans Serif

Colors
0094D4
00A9DD
6FCCEA
C7EBF8
E9F6FB
00AB8E
00BBA5
67D7C9
C6EFE9
E9F9F6

Requirements
Must have
• A stunning, elegant and modern look
Nice to have
• Inspiration from the colors of our logo throughout the site, but in an elegant way
Should not have
• An overly classic look for swimming pool sites

```html
<!DOCTYPE html>
<html lang="en">
<head>
<meta charset="utf-8">
<title>Brisa Lagoon – Above-Ground Pools</title>
<link rel="stylesheet" href="https://fonts.googleapis.com/css2?family=Urbanist:wght@300;400;500&family=Open+Sans:wght@400;600&display=swap">
<style>
  :root{
    --blue-deep:#0094D4;
    --blue:#00A9DD;
    --blue-soft:#6FCCEA;
    --blue-pale:#C7EBF8;
    --blue-mist:#E9F6FB;
    --green:#00AB8E;
    --green-bright:#00BBA5;
    --green-soft:#67D7C9;
    --accent:#1AD3E6;
    --ink:#1f1f1f;
    --text:#3a3a3a;
    --line:#dedede;
    --white:#ffffff;
  }
  *{box-sizing:border-box;margin:0;padding:0}
  html,body{width:1200px;height:4286px;overflow:hidden}
  body{position:relative;background:var(--white);font-family:"Open Sans",Arial,sans-serif;color:var(--text)}
  .abs{position:absolute}
  h1,h2,h3,h4{font-family:"Urbanist",Arial,sans-serif;font-weight:400;color:var(--ink);text-transform:uppercase;letter-spacing:.5px}
  .btn{position:absolute;display:flex;align-items:center;justify-content:center;font-family:"Open Sans",Arial,sans-serif;font-size:14px;text-transform:uppercase;letter-spacing:.3px;text-decoration:none}
  .btn-fill{background:var(--accent);color:#0d3b44}
  .btn-line{border:2px solid var(--ink);color:var(--ink);background:transparent}
  .btn-line-white{border:2px solid var(--white);color:var(--white)}

  /* hero */
  .hero{left:0;top:0;width:1200px;height:642px;background:linear-gradient(180deg,#6f8f6a 0%,#4d6d48 30%,#2f6aa6 62%,#a15a33 78%,#7a3e22 100%)}
  .nav{left:112px;top:31px;display:flex;gap:20px;font-size:13px;color:var(--white)}
  .nav-logo{left:0;width:1200px;top:18px;text-align:center;font-family:"Urbanist",sans-serif;font-weight:300;font-size:26px;line-height:1.1;color:var(--white);letter-spacing:2px}
  .nav-tools{left:953px;top:28px;display:flex;gap:16px;align-items:center;color:var(--white);font-size:13px}
  .hero-kicker{left:0;width:1200px;top:238px;text-align:center;color:var(--white);font-size:44px;font-weight:300}
  .hero-title{left:0;width:1200px;top:296px;text-align:center;color:var(--white);font-size:86px;font-weight:400;line-height:1}
  .hero-arrow{top:313px}

  /* why choose */
  .why-title{left:113px;top:730px;width:600px;font-size:31px;line-height:48px}
  .card{top:849px;width:313px;height:327px}
  .card-body{position:absolute;left:25px;right:14px;bottom:26px;color:var(--white)}
  .card-body h3{color:var(--white);font-size:22px;margin-bottom:8px}
  .card-body p{font-size:11px;line-height:17px;margin-bottom:6px}
  .card-body a{font-size:12px;color:var(--white)}

  /* transform band */
  .band{left:0;top:1270px;width:1200px;height:512px;background:linear-gradient(90deg,#2aa7e4 0%,#45b8ee 45%,#5fc4f1 100%)}
  .band-figure{left:566px;top:1270px;width:634px;height:512px;background:radial-gradient(ellipse at 55% 45%,#f0c2a0 0%,#e3a987 28%,rgba(69,184,238,0) 62%)}
  .band-title{left:110px;top:1334px;width:500px;font-size:31px;line-height:44px}
  .band-text{left:110px;top:1480px;width:489px;font-size:15px;line-height:25.7px;text-align:justify;color:#1d2a33}

  /* feature rows */
  .feature-img{width:489px;height:463px}
  .feature{width:430px;text-align:center}
  .feature h2{font-size:31px;margin-bottom:28px}
  .feature p{font-size:15px;line-height:25.7px}
  .feature p a{color:var(--accent);text-decoration:none}
  .rule-v{width:1px;height:87px;background:#9a9a9a}

  /* contact */
  .contact-img{left:0;top:3025px;width:601px;height:513px;background:linear-gradient(170deg,#4f6b46 0%,#3f7fb7 35%,#21a5e6 58%,#c77a4b 72%,#a0552f 100%)}
  .contact-panel{left:601px;top:3025px;width:599px;height:513px;background:var(--green)}
  .contact-panel h2{position:absolute;left:71px;top:100px;color:var(--white);font-size:31px}
  .contact-panel p{position:absolute;left:71px;top:172px;width:400px;color:var(--white);font-size:15px;line-height:25.7px}

  /* footer */
  .tagline{left:0;width:1200px;top:3610px;text-align:center;font-size:31px}
  .rule-h{height:1px;background:var(--line);left:110px;width:978px}
  .f-col h4{font-size:21px;margin-bottom:14px}
  .f-col ul{list-style:none}
  .f-col li{font-size:15px;line-height:26px;color:#2b2b2b}
  .socials{display:flex;gap:14px;margin-top:6px}
  .socials span{width:13px;height:13px;border-radius:50%;background:var(--ink);display:block}
  .newsletter{left:825px;top:3817px;width:263px;height:47px;border:1px solid #cfcfcf;display:flex;align-items:center;justify-content:space-between;padding:0 14px;font-size:12px;color:#888}
  .brand-mark{left:0;width:1200px;top:3944px;text-align:center;font-family:"Urbanist",sans-serif;font-weight:300;font-size:106px;line-height:112px;color:var(--blue);letter-spacing:4px}
  .legal{left:113px;top:4240px;font-size:12px;color:#333}
  .payments{left:802px;top:4233px;display:flex;gap:6px}
  .payments span{width:43px;height:27px;border-radius:3px;background:var(--blue-pale);display:block}
</style>
</head>
<body>

<!-- Hero -->
<div class="abs hero" role="img" aria-label="Long in-ground style pool beside a wooden deck and glass house, surrounded by tropical greenery"></div>
<nav class="abs nav"><span>Home</span><span>Our Products</span><span>Our Projects</span><span>Contact Us</span></nav>
<div class="abs nav-logo">BRISA<br>LAGOON</div>
<div class="abs nav-tools">
  <span>EN
    <svg width="9" height="6" viewBox="0 0 9 6"><path d="M1 1l3.5 3.5L8 1" fill="none" stroke="#fff" stroke-width="1.5"/></svg>
  </span>
  <svg width="16" height="16" viewBox="0 0 16 16"><circle cx="6.5" cy="6.5" r="4.5" fill="none" stroke="var(--accent)" stroke-width="2.2"/><path d="M10 10l4.5 4.5" stroke="var(--accent)" stroke-width="2.4"/></svg>
  <svg width="14" height="16" viewBox="0 0 14 16"><circle cx="7" cy="4.5" r="3.8" fill="var(--accent)"/><path d="M0 16c0-5 3-7.5 7-7.5s7 2.5 7 7.5z" fill="var(--accent)"/></svg>
  <svg width="17" height="16" viewBox="0 0 17 16"><path d="M0 1h3l2 9h9l2-7H4.5" fill="none" stroke="var(--accent)" stroke-width="2"/><circle cx="6" cy="13.5" r="1.6" fill="var(--accent)"/><circle cx="13" cy="13.5" r="1.6" fill="var(--accent)"/></svg>
</div>
<h2 class="abs hero-kicker">Welcome to</h2>
<h1 class="abs hero-title">Brisa Lagoon</h1>
<a class="btn btn-fill" style="left:532px;top:411px;width:135px;height:48px">Learn More</a>
<svg class="abs hero-arrow" style="left:45px" width="68" height="40" viewBox="0 0 68 40"><path d="M66 20H4M22 2L4 20l18 18" fill="none" stroke="#fff" stroke-width="3"/></svg>
<svg class="abs hero-arrow" style="left:1087px" width="68" height="40" viewBox="0 0 68 40"><path d="M2 20h62M46 2l18 18-18 18" fill="none" stroke="#fff" stroke-width="3"/></svg>

<!-- Why choose -->
<h2 class="abs why-title">Why choose our above-ground pools?</h2>
<a class="btn btn-fill" style="left:953px;top:752px;width:135px;height:47px">View More</a>

<div class="abs card" style="left:111px;background:linear-gradient(160deg,#9fd3ea 0%,#5fb6dc 50%,#2d7fae 100%)" role="img" aria-label="Striped beach ball floating on clear pool water">
  <div class="card-body"><h3>Superior Quality</h3><p>Each pool is constructed with high-quality materials, ensuring exceptional durability and strength.</p><a>Learn more</a></div>
</div>
<div class="abs card" style="left:444px;background:linear-gradient(160deg,#cfd8d6 0%,#2fa6b3 45%,#14707e 100%)" role="img" aria-label="Aerial view of a curved turquoise pool with white surround">
  <div class="card-body"><h3>Elegant Design</h3><p>Our pools come in a variety of styles and finishes, seamlessly blending into any garden setting.</p><a>Learn more</a></div>
</div>
<div class="abs card" style="left:775px;background:linear-gradient(180deg,#7a5a40 0%,#4c3a2c 45%,#1e2a33 100%)" role="img" aria-label="Indoor pool inside a wood-framed glass pavilion">
  <div class="card-body"><h3>Easy Installation</h3><p>Enjoy your new oasis quickly with our simple and fast installation process.</p><a>Learn more</a></div>
</div>

<!-- Transform band -->
<div class="abs band" role="img" aria-label="Bright blue pool water"></div>
<div class="abs band-figure" role="img" aria-label="Child in sunglasses resting at the pool edge"></div>
<h2 class="abs band-title">Transform your garden with our premium above-ground pools!</h2>
<p class="abs band-text">Achieve your dreams with our custom, tailor-made above-ground pools. Imagine an exceptional relaxation and leisure space right in your own backyard. With our unparalleled expertise and commitment to excellence, we create above-ground pools that exceed all expectations. Our exclusive, custom-designed models are crafted to combine style, durability, and innovation, offering a unique and refined experience.</p>
<a class="btn btn-line" style="left:110px;top:1687px;width:136px;height:44px;border-color:#1d2a33">View More</a>

<!-- Personalized services -->
<div class="abs feature-img" style="left:110px;top:1909px;background:linear-gradient(180deg,#8fc3ea 0%,#a17a55 35%,#7e6a4f 55%,#2ab6e0 70%,#6fd3ef 100%)" role="img" aria-label="Backyard above-ground pool with wooden pergola and deck"></div>
<div class="abs feature" style="left:642px;top:1944px">
  <h2>Personalized Services</h2>
  <p>We understand that every garden and client is unique. That's why we offer personalized services, from design to installation and after-sales support. Our team of experts is here to answer all your questions and guide you throughout your project.</p>
</div>
<div class="abs rule-v" style="left:857px;top:2170px"></div>
<a class="btn btn-line" style="left:790px;top:2285px;width:135px;height:45px">View More</a>

<!-- Guaranteed satisfaction -->
<div class="abs feature" style="left:124px;top:2485px">
  <h2>Guaranteed Satisfaction</h2>
  <p>Your satisfaction is our top priority. We are committed to providing you with exceptional service and the highest quality products. Join our community of satisfied customers who are already enjoying their custom above-ground pools. <a>10-Year Warranty!</a></p>
</div>
<div class="abs rule-v" style="left:340px;top:2709px"></div>
<a class="btn btn-line" style="left:273px;top:2824px;width:135px;height:45px">View More</a>
<div class="abs feature-img" style="left:601px;top:2449px;background:linear-gradient(160deg,#9fb8c9 0%,#2b63b0 35%,#164fa0 70%,#0e3d86 100%)" role="img" aria-label="White ladder in a deep blue above-ground pool"></div>

<!-- Contact -->
<div class="abs contact-img" role="img" aria-label="Oval pool set in a wooden deck with plants and a garden statue"></div>
<div class="abs contact-panel">
  <h2>Contact us today</h2>
  <p>Don't wait any longer to transform your garden into a wellness oasis. Contact us today to discover our range of customizable above-ground pools and get a tailored quote. Dive into a world of infinite possibilities with Brisa Lagoon.</p>
  <a class="btn btn-line-white" style="left:71px;top:326px;width:137px;height:44px">Contact</a>
</div>

<!-- Footer -->
<h2 class="abs tagline">We bring your pool dreams to life!</h2>
<div class="abs rule-h" style="top:3704px"></div>

<div class="abs f-col" style="left:110px;top:3764px"><h4>Company</h4><ul><li>Contact Us</li><li>Gift Card</li><li>Blog</li><li>Lookbook</li><li>Sustainability</li></ul></div>
<div class="abs f-col" style="left:283px;top:3764px"><h4>Get Help</h4><ul><li>FAQ</li><li>Terms of Service</li><li>Return Policy</li><li>Shipping Info</li></ul></div>
<div class="abs f-col" style="left:464px;top:3764px"><h4>Account</h4><ul><li>Log In</li><li>Sign Up</li><li>Gift Card</li></ul></div>
<div class="abs f-col" style="left:624px;top:3764px"><h4>Connect</h4><div class="socials"><span></span><span></span><span></span><span></span><span></span></div></div>
<div class="abs f-col" style="left:824px;top:3764px"><h4>Sign up to our newsletter</h4></div>
<div class="abs newsletter"><span>Email Address</span>
  <svg width="24" height="12" viewBox="0 0 24 12"><path d="M0 6h22M17 1l5 5-5 5" fill="none" stroke="#555" stroke-width="1.4"/></svg>
</div>

<div class="abs brand-mark">BRISA<br>LAGOON</div>

<div class="abs rule-h" style="top:4207px"></div>
<div class="abs legal">©Copyrights 2024 Company Name &nbsp;|&nbsp;&nbsp; All Rights Reserved</div>
<div class="abs payments"><span></span><span></span><span></span><span></span><span></span><span></span></div>

</body>
</html>
```